Corven Hale Interiors Web Site

We are looking at web site for our start-up company which is located in Abu Dhabi United Arab Emirates. Our main business activity is Interior fit out for high medium to high end projects in residential, corporate and hospitality.
In terms of look and feel the web site should be vibrant yet professional reflecting the artistic/construction nature of our business and built along or allows the following aspects:
- Number of Pages: 8-10 main pages (Including 10 Sub Pages)
- A custom responsive web design compatible with all browsers
- Dynamic (admin panel). CMS
- Anti Spam Online Forms
- Photo & Video Gallery
- Mobile Ready (Iphone,Android)]
- Social Media Integration
- Google Map
- Banner Artworks

```html
<!DOCTYPE html>
<html lang="en">
<head>
<meta charset="utf-8">
<title>Corven Hale Interiors</title>
<link href="https://fonts.googleapis.com/css2?family=Quicksand:wght@400;500;600;700&display=swap" rel="stylesheet">
<style>
:root{
  --navy:#0f3a52;
  --navy-deep:#0b2f44;
  --steel:#4c7d97;
  --steel-light:#5d8ba4;
  --nav-active:#5a87a1;
  --white:#ffffff;
  --ink:#333d44;
  --muted:#6a7780;
  --blue-icon:#1a9ed9;
  --teal-icon:#27b3b0;
  --orange-icon:#f4a623;
  --tab-grey:#dfe3e6;
}
*{margin:0;padding:0;box-sizing:border-box}
html,body{width:1200px;height:2679px;overflow:hidden}
body{font-family:"Quicksand",sans-serif;color:var(--ink);background:var(--white);position:relative}
section,header,nav,footer{position:absolute;left:0;width:1200px}
.upper{text-transform:uppercase}

/* hero */
.hero{top:0;height:497px;background:linear-gradient(100deg,#d9d2c4 0%,#c9bca6 30%,#e9e3d8 60%,#f1ede6 100%)}
.hero-photo{position:absolute;inset:0;background:
  radial-gradient(ellipse 380px 120px at 200px 280px,#7dc4c9 0%,rgba(125,196,201,0) 100%),
  radial-gradient(ellipse 240px 80px at 1000px 400px,#f5f2ee 0%,rgba(245,242,238,0) 100%),
  linear-gradient(180deg,rgba(255,255,255,0) 60%,rgba(190,180,168,.5) 100%)}
.brand-box{position:absolute;left:496px;top:0;width:208px;height:125px;background:linear-gradient(160deg,#3e6a82,#244b62);display:flex;flex-direction:column;align-items:center;justify-content:center;gap:8px;box-shadow:0 2px 6px rgba(0,0,0,.25)}
.brand-box .mark{width:30px;height:30px;background:var(--white);opacity:.85}
.brand-box .name{color:var(--white);font-weight:600;font-size:19px;letter-spacing:.3px}
.hero-title{position:absolute;top:210px;left:0;width:1200px;text-align:center;color:#123049;font-size:41px;font-weight:500;letter-spacing:1px}
.hero-sub{position:absolute;top:260px;left:290px;width:620px;text-align:center;color:var(--white);font-size:23px;line-height:29px;font-weight:600;text-shadow:0 1px 3px rgba(0,0,0,.35)}
.hero-btn{position:absolute;left:520px;top:371px;width:160px;height:40px;border:2px solid var(--white);background:rgba(20,45,60,.45);color:var(--white);font-size:15px;display:flex;align-items:center;justify-content:center;letter-spacing:.5px}
.hero-dots{position:absolute;top:462px;left:570px;display:flex;gap:8px}
.hero-dots span{width:10px;height:10px;border-radius:50%;background:var(--navy-deep)}
.hero-dots span:first-child{background:#4c8fb3}

/* nav */
.main-nav{top:497px;height:48px;background:var(--navy)}
.main-nav ul{list-style:none;display:flex;position:absolute;left:73px;top:0;height:48px}
.main-nav li{color:var(--white);font-size:14px;font-weight:500;height:48px;display:flex;align-items:center;padding:0 20px;margin-right:30px}
.main-nav li.active{background:var(--nav-active)}
.nav-phone{position:absolute;right:73px;top:0;height:48px;display:flex;align-items:center;gap:12px;color:var(--white);font-size:20px}

/* welcome */
.welcome{top:545px;height:275px;text-align:center}
.section-title{font-size:28px;font-weight:500;color:var(--navy);letter-spacing:.5px}
.welcome .section-title{position:absolute;top:42px;width:100%}
.welcome p{position:absolute;top:96px;left:73px;width:1054px;font-size:13px;line-height:25px;color:var(--muted)}
.btn{position:absolute;background:var(--steel);color:var(--white);font-size:16px;display:flex;align-items:center;justify-content:center}
.welcome .btn{left:523px;top:189px;width:154px;height:50px}

/* services */
.services{top:820px;height:380px;background:var(--navy)}
.services .section-title{position:absolute;top:37px;width:100%;text-align:center;color:var(--white)}
.service{position:absolute;top:103px;width:330px;text-align:center}
.service .icon{width:94px;height:94px;border-radius:50%;margin:0 auto;display:flex;align-items:center;justify-content:center}
.service h3{margin-top:36px;font-size:16px;font-weight:500;color:#5ea9d3}
.service p{margin-top:8px;font-size:13px;line-height:23px;color:#dfe8ee}

/* gallery */
.gallery{top:1200px;height:532px;text-align:center}
.gallery .section-title{position:absolute;top:37px;width:100%}
.tabs{position:absolute;top:93px;left:0;width:100%;display:flex;justify-content:center;gap:8px}
.tabs span{font-size:12px;padding:0 12px;height:25px;line-height:25px;background:var(--tab-grey);color:var(--ink)}
.tabs span.active{background:var(--steel);color:var(--white)}
.grid{position:absolute;left:73px;top:161px;width:1054px;height:325px;display:grid;grid-template-columns:repeat(4,1fr);grid-template-rows:repeat(2,1fr);gap:2px}
.tile{position:relative;display:flex;align-items:center;justify-content:center}

/* news band */
.band{top:1732px;height:379px;background:var(--steel)}
.col{position:absolute;top:34px;width:330px;color:var(--white)}
.col h2{font-size:26px;font-weight:500;margin-bottom:16px}
.entry{height:100px}
.entry .meta{font-size:11px;font-weight:600;margin-bottom:5px}
.entry p{font-size:11px;line-height:19px;color:#d7e5ee}
.entry p.quote{font-style:italic}
.blog-entry{display:flex;gap:14px;height:100px}
.blog-entry .thumb{width:78px;height:60px;flex:none}

/* contact */
.contact{top:2111px;height:403px}
.contact-info{position:absolute;left:0;top:0;width:282px;height:403px;background:var(--white);padding:38px 0 0 73px}
.contact-info h2{font-size:28px;font-weight:500;color:var(--navy)}
.contact-info .brand-line{display:flex;align-items:center;gap:8px;margin-top:18px;font-size:18px;font-weight:600;color:var(--navy)}
.contact-info .brand-line span.sq{width:12px;height:12px;background:var(--navy)}
.contact-info address{font-style:normal;margin-top:34px;font-size:12.5px;line-height:21px;color:var(--ink)}
.map{position:absolute;left:282px;top:0;width:918px;height:403px;background:linear-gradient(120deg,#8fb0c9 0%,#a8c2d4 40%,#d9d4c6 65%,#e7e1d2 100%)}
.form-box{position:absolute;left:304px;top:77px;width:396px;height:250px;background:rgba(110,140,175,.85);padding:14px}
.field{position:absolute;background:var(--white);font-size:12px;color:#8a8f94;padding:0 12px;display:flex;align-items:center}
.submit{position:absolute;left:232px;top:198px;width:152px;height:50px;background:#101418;color:var(--white);font-size:16px;display:flex;align-items:center;justify-content:center}

/* footer */
.site-footer{top:2514px;height:165px;background:var(--navy-deep)}
.foot-nav{position:absolute;left:73px;top:36px;display:flex;gap:28px;list-style:none}
.foot-nav li{color:#8fb0c6;font-size:13px}
.foot-mark{position:absolute;left:73px;top:76px;width:66px;height:66px;background:#3d6a85}
.copyright{position:absolute;left:164px;top:95px;font-size:11px;line-height:22px;color:#c5d3dc}
.connect{position:absolute;left:946px;top:28px}
.connect h4{font-size:13px;font-weight:500;color:var(--white)}
.socials{display:flex;gap:9px;margin-top:14px}
.socials span{width:30px;height:30px;border-radius:50%}
</style>
</head>
<body>

<header class="hero">
  <div class="hero-photo" role="img" aria-label="Bright living room with a turquoise sofa, striped cushions and a vase of flowers on a white side table"></div>
  <div class="brand-box">
    <span class="mark"></span>
    <span class="name">Corven Hale Interiors</span>
  </div>
  <h1 class="hero-title upper">Duis aliquam nibh a dui iaculis</h1>
  <p class="hero-sub">Aenean a nibh eget turpis vehicula tempus ac sed massa. Vestibulum dolor nulla, ultrices ac tincidunt sed, laoreet non est.</p>
  <div class="hero-btn upper">View Gallery</div>
  <div class="hero-dots"><span></span><span></span><span></span><span></span></div>
</header>

<nav class="main-nav">
  <ul class="upper">
    <li class="active">Home</li><li>About Us</li><li>Gallery</li><li>Blog</li><li>Services</li><li>Contacts</li>
  </ul>
  <div class="nav-phone">
    <svg width="18" height="18" viewBox="0 0 24 24"><path fill="#e04a3a" d="M6.6 10.8a15.1 15.1 0 006.6 6.6l2.2-2.2c.3-.3.7-.4 1-.2 1.1.4 2.3.6 3.6.6.6 0 1 .4 1 1V20c0 .6-.4 1-1 1A17 17 0 013 4c0-.6.4-1 1-1h3.5c.6 0 1 .4 1 1 0 1.3.2 2.5.6 3.6.1.3 0 .7-.2 1z"/></svg>
    <span>TEL: 555-010-2468</span>
  </div>
</nav>

<section class="welcome">
  <h2 class="section-title upper">Welcome to our website</h2>
  <p>Aliquam molestie, mi et imperdiet euismod, dui purus auctor tellus, et interdum lacus lectus et ante. Sed accumsan sollicitudin sapien, sit amet adipiscing turpis gravida ac. In congue, neque ac lobortis volutpat, libero mauris varius mi, vitae suscipit ipsum ligula vitae risus. Duis aliquam nibh a dui iaculis viverra id a velit. Vivamus egestas risus in magna varius commodo. Sed semper viverra egestas. Etiam pretium porttitor lectus, vel ornare neque porta volutpat.</p>
  <div class="btn upper">Read More ››</div>
</section>

<section class="services">
  <h2 class="section-title upper">What we do</h2>
  <div class="service" style="left:73px">
    <div class="icon" style="background:var(--blue-icon)">
      <svg width="40" height="36" viewBox="0 0 24 22"><path fill="#fff" d="M12 2L1 11h3v9h6v-6h4v6h6v-9h3z"/></svg>
    </div>
    <h3 class="upper">Heading goes here</h3>
    <p>Aliquam molestie, mi et imperdiet euismod, dui purus auctor tellus, et interdum lacus lectus et ante. Sed accumsan sollicitudin sapien, sit amet adipiscing turpis gravida ac.</p>
  </div>
  <div class="service" style="left:435px">
    <div class="icon" style="background:var(--teal-icon)">
      <svg width="44" height="34" viewBox="0 0 26 20"><rect x="4" y="2" width="18" height="12" rx="1" fill="none" stroke="#fff" stroke-width="2"/><path fill="#fff" d="M1 16h24v2H1z"/></svg>
    </div>
    <h3 class="upper">Heading goes here</h3>
    <p>Aliquam molestie, mi et imperdiet euismod, dui purus auctor tellus, et interdum lacus lectus et ante. Sed accumsan sollicitudin sapien, sit amet adipiscing turpis gravida ac.</p>
  </div>
  <div class="service" style="left:796px">
    <div class="icon" style="background:var(--orange-icon)">
      <svg width="42" height="36" viewBox="0 0 24 20"><rect x="2" y="2" width="20" height="16" fill="none" stroke="#fff" stroke-width="2"/><circle cx="8" cy="7" r="2" fill="#fff"/><path fill="#fff" d="M4 16l5-5 3 3 4-5 4 7z"/></svg>
    </div>
    <h3 class="upper">Heading goes here</h3>
    <p>Aliquam molestie, mi et imperdiet euismod, dui purus auctor tellus, et interdum lacus lectus et ante. Sed accumsan sollicitudin sapien, sit amet adipiscing turpis gravida ac.</p>
  </div>
</section>

<section class="gallery">
  <h2 class="section-title upper">Our gallery</h2>
  <div class="tabs upper"><span class="active">All</span><span>Photos</span><span>Videos</span></div>
  <div class="grid">
    <div class="tile" style="background:linear-gradient(160deg,#7fa06a,#5a5a5c 60%,#b34a4a)" role="img" aria-label="Outdoor terrace with wicker chairs and a set table"></div>
    <div class="tile" style="background:linear-gradient(160deg,#d9d2c4,#34466a 70%)" role="img" aria-label="Lounge with navy sofa and framed art, video">
      <svg width="44" height="44" viewBox="0 0 44 44"><circle cx="22" cy="22" r="20" fill="none" stroke="#fff" stroke-width="3"/><path d="M17 13l13 9-13 9z" fill="#fff"/></svg>
    </div>
    <div class="tile" style="background:linear-gradient(160deg,#c9d63a,#e8e26a 50%,#a6a36c)" role="img" aria-label="Lime green kitchen counter with fruit bowl"></div>
    <div class="tile" style="background:linear-gradient(160deg,#b9bcbd,#e3e1dc 60%,#c86d3a)" role="img" aria-label="Vase of flowers on a grey shelf, video">
      <svg width="44" height="44" viewBox="0 0 44 44"><circle cx="22" cy="22" r="20" fill="none" stroke="#fff" stroke-width="3"/><path d="M17 13l13 9-13 9z" fill="#fff"/></svg>
    </div>
    <div class="tile" style="background:linear-gradient(160deg,#e0601f,#c04a1a 60%,#6a3a1e)" role="img" aria-label="Orange wall with vases on a wooden sideboard"></div>
    <div class="tile" style="background:linear-gradient(160deg,#5c4634,#d6cbb7 55%,#8a6a4c)" role="img" aria-label="Bedroom with cream bedding and wooden bed frame"></div>
    <div class="tile" style="background:linear-gradient(160deg,#cfcfcf,#f0efed 50%,#6b6b6b)" role="img" aria-label="Monochrome dressing area with framed prints, video">
      <svg width="44" height="44" viewBox="0 0 44 44"><circle cx="22" cy="22" r="20" fill="none" stroke="#fff" stroke-width="3"/><path d="M17 13l13 9-13 9z" fill="#fff"/></svg>
    </div>
    <div class="tile" style="background:linear-gradient(160deg,#eef0d0,#e64a9a 45%,#9ecf3a)" role="img" aria-label="Colourful pink and green cube shelves with toys"></div>
  </div>
</section>

<section class="band">
  <div class="col" style="left:73px">
    <h2 class="upper">Our news</h2>
    <div class="entry"><div class="meta upper">Aug 31, 2014</div><p>Lorem ipsum dolor sit amet, consectetuer adipiscing elit. Praesent vestibulum molestie lacus. Aenean nonummy hendrerit mauris. Phasellus porta.</p></div>
    <div class="entry"><div class="meta upper">Aug 31, 2014</div><p>Lorem ipsum dolor sit amet, consectetuer adipiscing elit. Praesent vestibulum molestie lacus. Aenean nonummy hendrerit mauris. Phasellus porta.</p></div>
    <div class="entry"><div class="meta upper">Aug 31, 2014</div><p>Lorem ipsum dolor sit amet, consectetuer adipiscing elit. Praesent vestibulum molestie lacus. Aenean nonummy hendrerit mauris. Phasellus porta.</p></div>
  </div>
  <div class="col" style="left:436px">
    <h2 class="upper">Testimonials</h2>
    <div class="entry"><div class="meta upper">Mara Quill</div><p class="quote">"Lorem ipsum dolor sit amet, consectetuer adipiscing elit. Praesent vestibulum molestie lacus. Aenean nonummy hendrerit mauris....".</p></div>
    <div class="entry"><div class="meta upper">Mara Quill</div><p class="quote">"Lorem ipsum dolor sit amet, consectetuer adipiscing elit. Praesent vestibulum molestie lacus. Aenean nonummy hendrerit mauris....".</p></div>
    <div class="entry"><div class="meta upper">Mara Quill</div><p class="quote">"Lorem ipsum dolor sit amet, consectetuer adipiscing elit. Praesent vestibulum molestie lacus. Aenean nonummy hendrerit mauris....".</p></div>
  </div>
  <div class="col" style="left:795px">
    <h2 class="upper">Blog</h2>
    <div class="blog-entry"><div class="thumb" style="background:linear-gradient(135deg,#d9443a,#3a7ab0)" role="img" aria-label="Colourful room thumbnail"></div><div class="entry"><div class="meta upper">Fusce suscipit varius mi...</div><p>Lorem ipsum dolor sit amet, consectetuer adipiscing elit. Praesent vestibulum molestie lacus...</p></div></div>
    <div class="blog-entry"><div class="thumb" style="background:linear-gradient(135deg,#c9b8a0,#b0503a)" role="img" aria-label="Living room thumbnail"></div><div class="entry"><div class="meta upper">Fusce suscipit varius mi...</div><p>Lorem ipsum dolor sit amet, consectetuer adipiscing elit. Praesent vestibulum molestie lacus...</p></div></div>
    <div class="blog-entry"><div class="thumb" style="background:linear-gradient(135deg,#efe9df,#c46a3c)" role="img" aria-label="Bright interior thumbnail"></div><div class="entry"><div class="meta upper">Fusce suscipit varius mi...</div><p>Lorem ipsum dolor sit amet, consectetuer adipiscing elit. Praesent vestibulum molestie lacus...</p></div></div>
  </div>
</section>

<section class="contact">
  <div class="map" role="img" aria-label="Street map of Abu Dhabi with roads, islands and coastline"></div>
  <div class="contact-info">
    <h2 class="upper">Contact us</h2>
    <div class="brand-line"><span class="sq"></span>Corven Hale Interiors</div>
    <address>P.O. Box 5120 Abu Dhabi-UAE<br>Tel: +971 2 555 0142<br>Fax: +971 2 555 0143<br>Email: hello@corvenhale.example</address>
  </div>
  <form class="form-box">
    <div class="field" style="left:14px;top:14px;width:180px;height:36px">Name</div>
    <div class="field" style="left:204px;top:14px;width:180px;height:36px">Contact No.</div>
    <div class="field" style="left:14px;top:60px;width:180px;height:36px">Email Address</div>
    <div class="field" style="left:204px;top:60px;width:180px;height:36px">City</div>
    <div class="field" style="left:14px;top:106px;width:370px;height:66px;align-items:flex-start;padding-top:10px">Email Address</div>
    <div class="submit upper">Submit Now ››</div>
  </form>
</section>

<footer class="site-footer">
  <ul class="foot-nav upper">
    <li>Home</li><li>About Us</li><li>Gallery</li><li>Blog</li><li>Services</li><li>Contacts</li>
  </ul>
  <div class="foot-mark"></div>
  <p class="copyright upper">Copyright © 2014. Company Name. All right reserved<br>Terms of services</p>
  <div class="connect">
    <h4 class="upper">Connect us</h4>
    <div class="socials">
      <span style="background:#3b5b99"></span>
      <span style="background:#2fa3dc"></span>
      <span style="background:#6d6d6d"></span>
      <span style="background:#f08a24"></span>
      <span style="background:#d93b2b"></span>
    </div>
  </div>
</footer>

</body>
</html>
```